TREVAL BUILDWORKS, LLC Webpage portfolio

I want to create a Website that allows my potential clients to browse my Skilled work via before and after photos. I want the website to enhance the work that I provide and potentially drive new business, or at least solidify my work.
I also do 3D CAD and Modeling of New Spaces and it would be nice to show some of that work from pencil design to 3D modeling, which I feel may help give me more clients.

The website needs to show a solid carpenter/company with the skills to get any project completed.

Types of Jobs - Custom Carpentry & Finishes, Kitchens, Baths, Basements, Decks, Porches, Whole House Renovation - Skilled Craftsmanship (Hardwood Flooring, Floor and Wall Tile) and much more...

Target Market(s)

Residential Home Renovation, Kitchen and Bath Renovation, Home Improvement

Industry/Entity Type

Residential Construction

Number of Pages Required

5+ page

Font styles to use
Sans Serif
Script

Requirements
Must have
• Similar to Plinvo.com, except for Treval Buildworks.
• Must be inviting.
• My Services Offered
• A way to reach me or contact me for estimates with some sort of Screening Questionare.
Nice to have
• Inviting Colors
Should not have
• Not sure at this time

```html
<!DOCTYPE html>
<html lang="en">
<head>
<meta charset="utf-8">
<title>Treval Buildworks — Design, Build &amp; Remodeling</title>
<link href="https://fonts.googleapis.com/css2?family=Questrial&family=Open+Sans:wght@400;600&display=swap" rel="stylesheet">
<style>
:root{
  --blue:#2a9fd8;
  --navy:#1d4f73;
  --ink:#3a3a3a;
  --muted:#8a8a8a;
  --line:#e2e2e2;
  --band:#f7f7f7;
  --band-dark:#ececec;
  --footer:#f5f5f5;
  --white:#ffffff;
}
*{box-sizing:border-box;margin:0;padding:0}
html,body{width:1200px;height:3061px;overflow:hidden;background:var(--white)}
body{position:relative;font-family:"Open Sans",Arial,sans-serif;color:var(--ink)}
.abs{position:absolute}
.display{font-family:"Questrial",Arial,sans-serif;font-weight:400}
a{color:inherit;text-decoration:none}

/* header */
.site-header{position:absolute;left:0;top:0;width:1200px;height:118px;background:var(--white)}
.brand{position:absolute;left:133px;top:40px;display:flex;align-items:center;gap:10px;
  font-family:"Questrial",sans-serif;font-size:27px;color:var(--navy)}
.brand .mark{width:22px;height:22px;background:var(--navy)}
.search{position:absolute;left:812px;top:29px;width:253px;height:30px;border:1px solid var(--line);
  font-size:11px;color:#555;padding:7px 12px}
.search svg{position:absolute;right:10px;top:7px}
.main-nav{position:absolute;top:88px;left:0;width:1200px;font-size:11px;font-weight:600;color:#333}
.main-nav a{position:absolute;transform:translateX(-50%);white-space:nowrap;letter-spacing:.3px}
.main-nav a.active{color:var(--blue)}
.main-nav a.active::after{content:"";position:absolute;left:-6px;right:-6px;top:26px;height:3px;background:var(--blue)}

/* hero */
.hero{position:absolute;left:0;top:118px;width:1200px;height:470px;
  background:linear-gradient(100deg,#5e636a 0%,#8d8f90 25%,#b7b5ae 45%,#7a5b45 62%,#a99e8f 75%,#dfe3e8 100%)}
.hero-title{position:absolute;left:0;width:1200px;top:165px;text-align:center;color:var(--white);font-size:54px}
.btn{position:absolute;background:var(--blue);color:var(--white);font-size:13px;text-align:center;
  letter-spacing:.5px;display:flex;align-items:center;justify-content:center}
.dots{position:absolute;top:430px;left:570px;display:flex;gap:6px}
.dots span{width:10px;height:10px;border-radius:50%;background:rgba(255,255,255,.55)}
.dots span:first-child{background:var(--white)}

/* section headings */
.section-title{position:absolute;left:0;width:1200px;text-align:center;font-size:29px;color:#444}

/* features */
.feature{position:absolute;width:300px;text-align:center;transform:translateX(-50%)}
.feature svg{display:block;margin:0 auto}
.feature h3{font-family:"Questrial",sans-serif;font-weight:400;font-size:19px;color:#444;margin-top:24px}
.feature p{font-size:11px;color:var(--muted);line-height:21px;margin-top:14px}

/* services */
.services{position:absolute;left:0;top:1067px;width:1200px;height:613px;background:var(--band)}
.card{position:absolute;top:153px;width:292px;height:388px;background:var(--white);text-align:center}
.card .photo{width:100%;height:192px}
.card h3{font-family:"Questrial",sans-serif;font-weight:400;font-size:19px;color:#444;margin-top:36px}
.card p{font-size:11px;color:var(--muted);line-height:21px;margin:22px 28px 0}
.card .more{display:block;font-size:10px;color:#666;margin-top:16px;letter-spacing:.3px}
.arrow{position:absolute;top:336px}

/* recent work */
.tile{position:absolute}
.tile span{position:absolute;left:30px;top:22px;color:var(--white);font-family:"Questrial",sans-serif;font-size:19px}

/* before & after */
.ba{position:absolute;left:0;top:2327px;width:1200px;height:404px;background:var(--band-dark)}
.shot{position:absolute;top:130px;height:203px}
.shot .tag{position:absolute;left:0;bottom:0;width:98px;height:29px;background:var(--blue);color:var(--white);
  font-size:11px;padding:7px 0 0 34px}

/* footer */
.site-footer{position:absolute;left:0;top:2731px;width:1200px;height:330px;background:var(--footer)}
.footer-brand{position:absolute;left:133px;top:62px;font-family:"Questrial",sans-serif;font-size:25px;color:var(--navy)}
.social{position:absolute;left:133px;top:144px;display:flex;gap:8px}
.social span{width:30px;height:30px;border:1.5px solid #333;border-radius:50%}
.footer-col h4{position:absolute;top:44px;font-family:"Questrial",sans-serif;font-weight:400;font-size:15px;color:#333}
.quick-links{position:absolute;left:404px;top:88px;list-style:none;font-size:11px;color:#444;line-height:24px}
.news-copy{position:absolute;left:565px;top:86px;width:260px;font-size:11px;color:#555;line-height:24px}
.news-input{position:absolute;left:565px;top:151px;width:249px;height:39px;background:var(--white);
  border:1px solid var(--line);font-size:11px;color:#555;padding:11px 16px}
.contact-list{position:absolute;left:904px;top:86px;list-style:none;font-size:11px;color:#444}
.contact-list li{position:relative;padding-left:26px;height:27px;line-height:18px}
.contact-list li svg{position:absolute;left:0;top:3px}
.contact-list li.addr{line-height:19px;height:auto}
.footer-rule{position:absolute;left:133px;top:273px;width:932px;height:1px;background:#d8d8d8}
.copyright{position:absolute;left:0;top:293px;width:1200px;text-align:center;font-size:11px;color:var(--muted)}
</style>
</head>
<body>

<header class="site-header">
  <a class="brand"><span class="mark"></span>Treval Buildworks</a>
  <div class="search">Search...
    <svg width="14" height="14" viewBox="0 0 14 14" fill="none" stroke="#777" stroke-width="1.4"><circle cx="6" cy="6" r="4.5"/><path d="M9.5 9.5L13 13"/></svg>
  </div>
  <nav class="main-nav">
    <a class="active" style="left:657px">HOME</a>
    <a style="left:743px">ABOUT US</a>
    <a style="left:839px">SERVICES</a>
    <a style="left:931px">GALLERY</a>
    <a style="left:1031px">CONTACT US</a>
  </nav>
</header>

<section class="hero" role="img" aria-label="Photo of a renovated house porch with white railings and a stone column">
  <h1 class="hero-title display">Whole House Renovation</h1>
  <a class="btn" style="left:508px;top:266px;width:184px;height:45px">REQUEST QUOTE</a>
  <div class="dots"><span></span><span></span><span></span><span></span></div>
</section>

<section class="features">
  <h2 class="section-title display" style="top:628px">Create the home you've always wanted</h2>

  <div class="feature" style="left:255px;top:714px">
    <svg width="74" height="70" viewBox="0 0 74 70" fill="none" stroke="#666" stroke-width="2">
      <path d="M14 22 A28 28 0 0 1 60 22"/><path d="M60 48 A28 28 0 0 1 14 48"/>
      <path d="M56 14 L60 22 L52 23"/><path d="M18 56 L14 48 L22 47"/>
      <path d="M22 36 L37 22 L52 36 L48 36 L48 50 L26 50 L26 36 Z" fill="#666"/>
    </svg>
    <h3>Discover design ideas</h3>
    <p>Browse more than 12 million photos and filter<br>based on your taste</p>
  </div>

  <div class="feature" style="left:600px;top:714px">
    <svg width="74" height="70" viewBox="0 0 74 70" fill="none" stroke="#666" stroke-width="2">
      <path d="M14 38 L37 14 L48 25"/><path d="M20 34 L20 60 L34 60"/>
      <rect x="30" y="34" width="8" height="10"/><circle cx="50" cy="38" r="6"/>
      <path d="M40 62 L40 54 Q50 46 60 54 L60 62 Z"/><path d="M54 20 L54 12 L60 12 L60 26"/>
    </svg>
    <h3>Find home professionals</h3>
    <p>Browse more than 12 million photos and filter<br>based on your taste</p>
  </div>

  <div class="feature" style="left:945px;top:714px">
    <svg width="74" height="70" viewBox="0 0 74 70" fill="none" stroke="#666" stroke-width="2">
      <path d="M10 32 L37 10 L64 32"/><path d="M16 28 L16 62 L58 62 L58 28"/>
      <rect x="30" y="42" width="14" height="20"/><path d="M30 50 L44 50"/>
    </svg>
    <h3>Shop for your home</h3>
    <p>Browse more than 13 million photos and filter<br>based on your taste</p>
  </div>

  <a class="btn" style="left:516px;top:941px;width:168px;height:47px">GET STARTED</a>
</section>

<section class="services">
  <h2 class="section-title display" style="top:76px">Our Services</h2>
  <svg class="arrow" style="left:80px" width="16" height="26" viewBox="0 0 16 26" fill="none" stroke="#555" stroke-width="2"><path d="M13 2 L3 13 L13 24"/></svg>
  <svg class="arrow" style="left:1094px" width="16" height="26" viewBox="0 0 16 26" fill="none" stroke="#555" stroke-width="2"><path d="M3 2 L13 13 L3 24"/></svg>

  <article class="card" style="left:133px">
    <div class="photo" role="img" aria-label="Carpenter placing a spirit level on wooden boards" style="background:linear-gradient(135deg,#c48a52,#e2b47c 55%,#8a5a34)"></div>
    <h3>Custom Carpentry</h3>
    <p>Browse more than 12 million photos and filter based on your taste</p>
    <a class="more">READ MORE ›</a>
  </article>
  <article class="card" style="left:453px">
    <div class="photo" role="img" aria-label="Bright white kitchen with glossy counter and sink" style="background:linear-gradient(135deg,#cfd6dc,#f2f4f6 55%,#9aa3ab)"></div>
    <h3>Kitchens</h3>
    <p>Browse more than 12 million photos and filter based on your taste</p>
    <a class="more">READ MORE ›</a>
  </article>
  <article class="card" style="left:773px">
    <div class="photo" role="img" aria-label="Modern white bathroom with bathtub and glass shower" style="background:linear-gradient(135deg,#b9bfc4,#e9ebed 55%,#8f969c)"></div>
    <h3>Baths</h3>
    <p>Browse more than 12 million photos and filter based on your taste</p>
    <a class="more">READ MORE ›</a>
  </article>
</section>

<section class="recent-work">
  <h2 class="section-title display" style="top:1742px">Our Recent Work</h2>
  <div class="tile" role="img" aria-label="Renovated house exterior with grey siding" style="left:133px;top:1823px;width:447px;height:196px;background:linear-gradient(135deg,#6e7176,#9a9c9e 60%,#55585c)"><span>Whole House Renovation</span></div>
  <div class="tile" role="img" aria-label="Kitchen with granite island and wood cabinets" style="left:590px;top:1823px;width:233px;height:196px;background:linear-gradient(135deg,#3a2a20,#7a5638 60%,#2b1e16)"><span style="left:14px">Kitchens</span></div>
  <div class="tile" role="img" aria-label="Dark hardwood floor boards" style="left:833px;top:1823px;width:232px;height:196px;background:linear-gradient(135deg,#2a1d16,#5a3a28 60%,#1e1510)"><span style="left:14px">Hardwood Flooring</span></div>
  <div class="tile" role="img" aria-label="Room with new floor and wall tile and white cabinets" style="left:133px;top:2027px;width:349px;height:216px;background:linear-gradient(135deg,#5a4638,#8f7a66 55%,#4a3a2e)"><span style="left:34px">Floor and Wall Tile</span></div>
  <div class="tile" role="img" aria-label="3D model of a home floor plan" style="left:492px;top:2027px;width:573px;height:216px;background:linear-gradient(135deg,#5c5c5c,#c9c9c9 55%,#7a7a7a)"><span style="left:34px">3D modeling</span></div>
</section>

<section class="ba">
  <h2 class="section-title display" style="top:73px">Before and After</h2>
  <div class="shot" role="img" aria-label="Room before renovation with old wood panelling" style="left:133px;width:224px;background:linear-gradient(135deg,#3a2618,#6a4a30 60%,#2a1a10)"><span class="tag">before</span></div>
  <div class="shot" role="img" aria-label="Porch after renovation with white railings" style="left:367px;width:225px;background:linear-gradient(135deg,#6a6c70,#b0aca4 55%,#7a5a44)"><span class="tag">After</span></div>
  <div class="shot" role="img" aria-label="Kitchen before renovation" style="left:604px;width:227px;background:linear-gradient(135deg,#7a6a5a,#c8c0b4 55%,#6a4e38)"><span class="tag">before</span></div>
  <div class="shot" role="img" aria-label="Kitchen after renovation" style="left:841px;width:224px;background:linear-gradient(135deg,#6a5a4c,#cfc8bc 55%,#8a6a4c)"><span class="tag">After</span></div>
</section>

<footer class="site-footer">
  <div class="footer-brand">Treval Buildworks</div>
  <div class="social" aria-label="Social links"><span></span><span></span><span></span><span></span><span></span></div>

  <div class="footer-col"><h4 style="left:404px">Quick Links</h4></div>
  <ul class="quick-links">
    <li>Home</li><li>About us</li><li>Services</li><li>Gallery</li><li>Contact us</li>
  </ul>

  <div class="footer-col"><h4 style="left:565px">Newsletter</h4></div>
  <p class="news-copy">Enter your email address to receive the latest news and notes from our blog.</p>
  <div class="news-input">Enter Your Mail Id</div>
  <a class="btn" style="left:565px;top:210px;width:84px;height:29px;font-size:10px">SUBSCRIBE</a>

  <div class="footer-col"><h4 style="left:904px">Contact us</h4></div>
  <ul class="contact-list">
    <li><svg width="13" height="12" viewBox="0 0 13 12" fill="#444"><rect x="1" y="2" width="11" height="9" rx="1.5"/><rect x="3" y="0" width="7" height="3" rx="1"/></svg>(555) 014-4100</li>
    <li><svg width="13" height="12" viewBox="0 0 13 12" fill="#444"><rect x="0" y="4" width="13" height="8" rx="1"/><rect x="3" y="0" width="7" height="5"/></svg>(555) 014-4101</li>
    <li><svg width="13" height="11" viewBox="0 0 13 11" fill="none" stroke="#444" stroke-width="1.4"><rect x="1" y="1" width="11" height="9"/><path d="M1 1 L6.5 6 L12 1"/></svg><u>info@yourmailid.com</u></li>
    <li class="addr"><svg width="11" height="14" viewBox="0 0 11 14" fill="#444"><path d="M5.5 0 A5.5 5.5 0 0 1 11 5.5 C11 9 5.5 14 5.5 14 C5.5 14 0 9 0 5.5 A5.5 5.5 0 0 1 5.5 0 Z M5.5 3.5 A2 2 0 1 0 5.5 7.5 A2 2 0 1 0 5.5 3.5 Z"/></svg>#2868 Lorem ipsum dolor sit<br>amet, consectetur</li>
  </ul>

  <div class="footer-rule"></div>
  <p class="copyright">©2017 Treval Buildworks All Rights Reserved</p>
</footer>

</body>
</html>
```